Spring Style Exclusive Shopping Party for women

We need a postcard design for our Spring Shopping Event. Willow Lane is a women's apparel and accessories store featuring missy, petite and plus sizes. Event is Saturday, April 1 from 9am-10am. Looking for a twist on the spring shopping party idea. Attaching 2 postcards we have previously sent for this event and 2 ideas for what we are looking for in new postcard.

Target Market(s)

women 20+

Industry/Entity Type

Retail

Font styles to use
Serif

Requirements
Must have
• must be eye catching, have the logo, date and time of event,
Nice to have
• woman model

```html
<!DOCTYPE html>
<html lang="en">
<head>
<meta charset="utf-8">
<title>Willow Lane Spring Summer Shopping Event</title>
<link rel="stylesheet" href="https://fonts.googleapis.com/css2?family=Courgette&family=Cormorant+Garamond:ital,wght@1,600&family=Tenor+Sans&display=swap">
<style>
  :root {
    --sky: #dfe9f8;
    --blush: #f7dcf3;
    --petal: #e7b6e6;
    --orchid: #c98bd3;
    --lavender: #b9a6d6;
    --ink: #141414;
    --magenta: #f01bc8;
    --white: #ffffff;
    --photo-light: #e9dff0;
    --photo-mid: #c9b6c4;
    --photo-dark: #2a2328;
  }
  html, body {
    margin: 0;
    padding: 0;
    overflow: hidden;
  }
  .postcard {
    position: relative;
    width: 1200px;
    height: 927px;
    overflow: hidden;
    background:
      radial-gradient(ellipse at 20% 5%, var(--sky) 0%, transparent 45%),
      radial-gradient(ellipse at 75% 10%, var(--blush) 0%, transparent 50%),
      linear-gradient(180deg, #eef0fb 0%, #fbeefa 55%, #f6e4f6 100%);
  }
  .floral-backdrop {
    position: absolute;
    left: 0;
    top: 140px;
    width: 520px;
    height: 787px;
    background:
      radial-gradient(ellipse at 15% 85%, var(--orchid) 0%, transparent 55%),
      radial-gradient(ellipse at 35% 60%, var(--petal) 0%, transparent 60%),
      radial-gradient(ellipse at 10% 40%, rgba(201,139,211,0.5) 0%, transparent 50%);
    opacity: 0.85;
  }
  .floral-corner {
    position: absolute;
    right: 0;
    bottom: 0;
    width: 560px;
    height: 160px;
    background: radial-gradient(ellipse at 70% 100%, var(--lavender) 0%, transparent 65%);
    opacity: 0.7;
  }
  .model-photo {
    position: absolute;
    left: 720px;
    top: 64px;
    width: 456px;
    height: 863px;
    border-radius: 200px 200px 0 0;
    background: linear-gradient(180deg, var(--photo-light) 0%, var(--photo-mid) 40%, var(--white) 60%, var(--photo-dark) 78%, var(--photo-mid) 100%);
    opacity: 0.9;
  }
  .headline {
    position: absolute;
    left: 80px;
    top: 0;
    width: 600px;
    height: 927px;
  }
  .headline > * {
    position: absolute;
    left: 0;
    width: 100%;
    margin: 0;
    text-align: center;
    line-height: 1;
    white-space: nowrap;
  }
  .brand-name {
    top: 240px;
    font-family: "Courgette", cursive;
    font-weight: 400;
    font-size: 92px;
    color: var(--ink);
  }
  .presents {
    top: 406px;
    font-family: "Cormorant Garamond", serif;
    font-style: italic;
    font-weight: 600;
    font-size: 38px;
    color: var(--ink);
  }
  .event-season {
    top: 463px;
    font-family: "Courgette", cursive;
    font-weight: 400;
    font-size: 78px;
    color: var(--magenta);
  }
  .event-title {
    top: 578px;
    font-family: "Courgette", cursive;
    font-size: 58px;
    color: var(--ink);
  }
  .event-range {
    top: 676px;
    font-family: "Tenor Sans", sans-serif;
    font-variant: small-caps;
    font-size: 38px;
    letter-spacing: 4px;
    color: var(--ink);
  }
  .event-date {
    top: 752px;
    font-family: "Cormorant Garamond", serif;
    font-style: italic;
    font-weight: 600;
    font-size: 34px;
    color: var(--magenta);
  }
</style>
</head>
<body>
  <main class="postcard">
    <div class="floral-backdrop" role="img" aria-label="Soft pink and purple floral decoration"></div>
    <div class="floral-corner" role="img" aria-label="Pale lavender flower petals"></div>
    <div class="model-photo" role="img" aria-label="Photo of a woman in a white fringed top and black high-waisted shorts"></div>
    <section class="headline">
      <h1 class="brand-name">Willow Lane</h1>
      <p class="presents">Presents</p>
      <h2 class="event-season">Spring Summer</h2>
      <p class="event-title">Shopping Event</p>
      <p class="event-range">Apparel &amp; Accessories</p>
      <p class="event-date">Saturday, April 1 &middot; 9am – 10am</p>
    </section>
  </main>
</body>
</html>
```